Animal Eye Clinic needs a Business card

We are a new veterinary ophthalmology practice (Ridgeline Pet Vision Care) and we need a business card designed. We only see animal eyes - we are not a regular veterinary clinic. We already have a logo. We are looking for a professional, good looking business card to hand out to our clients. We are looking for something simple but professional and contemporary. Our logo is likely the only picture/graphic that needs to be on the card.
Updates

Contact Information for Business Card

Delia Vossman, BSc, DVM, MSc, DipACVO
Veterinary Ophthalmologist

Phone: 250.418.3927
Email: ridgelinepetvisioncare@mailbox-example.net
Website: ridgelinepetvisioncare-example.net
Address: 1874 Thornbury Rd
Kelowna, BC, V1X 4M9

Colors

Designer to choose colors to be used in the design.

Requirements
Must have
• Our logo (attached)

```html
<!DOCTYPE html>
<html lang="en">
<head>
<meta charset="utf-8">
<title>Ridgeline Pet Vision Care – Business Card</title>
<link href="https://fonts.googleapis.com/css2?family=Roboto:wght@400;500;700&display=swap" rel="stylesheet">
<style>
  :root {
    --backdrop: #3b3b3c;
    --card: #262627;
    --teal: #0e9bab;
    --ink: #f2f2f2;
    --muted: #cfcfcf;
    --rule: #bdbdbd;
  }
  * { box-sizing: border-box; margin: 0; padding: 0; }
  html, body {
    width: 1200px; height: 901px; overflow: hidden;
    background: var(--backdrop);
    font-family: "Roboto", Arial, sans-serif;
  }
  .sheet {
    position: relative; width: 1200px; height: 901px;
    display: flex; flex-direction: column; align-items: center;
    justify-content: center; gap: 56px;
  }
  .card {
    position: relative; width: 640px; height: 366px;
    background: var(--card);
    box-shadow: 0 10px 28px rgba(0,0,0,.45);
    overflow: hidden;
  }
  /* brand mark: name + plain circle */
  .brand { display: flex; align-items: center; gap: 14px; }
  .brand__dot {
    flex: none; border-radius: 50%; background: var(--teal);
  }
  .brand__name {
    color: var(--teal); font-weight: 700; line-height: 1.1;
    letter-spacing: .02em;
  }
  .card--front { display: flex; align-items: center; justify-content: center; }
  .card--front .brand__dot { width: 56px; height: 56px; }
  .card--front .brand__name { font-size: 30px; }

  .card--back { display: flex; align-items: center; padding: 0 28px 0 34px; }
  .card--back::after {
    content: ""; position: absolute; left: 0; right: 0; bottom: 0;
    height: 10px; background: var(--teal);
  }
  .card--back .brand { width: 232px; }
  .card--back .brand__dot { width: 44px; height: 44px; }
  .card--back .brand__name { font-size: 21px; }
  .divider {
    width: 1px; height: 176px; background: var(--rule);
    margin: 0 22px 0 14px; flex: none;
  }
  .contact { color: var(--ink); font-size: 14px; line-height: 1.3; }
  .contact__name { color: var(--teal); font-weight: 700; font-size: 17px; }
  .contact__creds { color: var(--teal); font-weight: 500; font-size: 11px; }
  .contact__title { font-size: 15px; margin-bottom: 10px; }
  .contact__address { font-size: 15px; margin-bottom: 10px; }
  .contact__line { display: flex; align-items: center; gap: 7px; font-size: 12.5px; }
  .contact__line svg { flex: none; width: 11px; height: 11px; fill: var(--teal); }
  .accent { color: var(--teal); }
</style>
</head>
<body>
<main class="sheet">
  <section class="card card--front" aria-label="Card front">
    <div class="brand">
      <span class="brand__dot"></span>
      <span class="brand__name">Ridgeline Pet Vision Care</span>
    </div>
  </section>

  <section class="card card--back" aria-label="Card back">
    <div class="brand">
      <span class="brand__dot"></span>
      <span class="brand__name">Ridgeline Pet Vision Care</span>
    </div>
    <span class="divider"></span>
    <div class="contact">
      <p><span class="contact__name">Delia Vossman</span><span class="contact__creds">, BSc, DVM, MSc, DipACVO</span></p>
      <p class="contact__title">Veterinary Ophthalmologist</p>
      <p class="contact__address">1874 Thornbury Rd<br>Kelowna, BC, V1X 4M9</p>
      <p class="contact__line">
        <svg viewBox="0 0 24 24"><path d="M6.6 10.8a15.1 15.1 0 0 0 6.6 6.6l2.2-2.2a1 1 0 0 1 1-.25 11.4 11.4 0 0 0 3.6.57 1 1 0 0 1 1 1V20a1 1 0 0 1-1 1A17 17 0 0 1 3 4a1 1 0 0 1 1-1h3.5a1 1 0 0 1 1 1c0 1.25.2 2.45.57 3.57a1 1 0 0 1-.25 1z"/></svg>
        250.418.3927
      </p>
      <p class="contact__line">
        <svg viewBox="0 0 24 24"><path d="M2 5h20v14H2z M2 5l10 8 10-8" /></svg>
        ridgelinepetvisioncare@mailbox-example.net
      </p>
      <p class="contact__line">
        <svg viewBox="0 0 24 24"><circle cx="12" cy="12" r="10"/></svg>
        <span>www.<span class="accent">ridgelinepetvisioncare-example</span>.net</span>
      </p>
    </div>
  </section>
</main>
</body>
</html>
```